Varnex Consulting Business card design.

See our website www.varnexconsulting.example which will give you a good idea of what we are about. The font is called 'Play'.

I'd like a standout business card in keeping with the themes and branding on the website

Target Market(s)

professionals. HR directors

Industry/Entity Type

Business

Contact Information for Business Card

Varnex Consulting PO Box 3172 Merrowdale NSW 2291 1300 485 193 Gavin Threlkeld Principal email: career@varnexconsulting.example ABN: 71203948865

Font styles to use
Other font styles liked:
• Play

Requirements
Must have
• Must have same design colours and branding as website.
• On back I'd prefer a list of the things we do which appears below the name at the header on the website

```html
<!DOCTYPE html>
<html lang="en">
<head>
<meta charset="utf-8">
<title>Varnex Consulting – Business Card</title>
<link href="https://fonts.googleapis.com/css2?family=Play:wght@400;700&display=swap" rel="stylesheet">
<style>
  :root {
    --navy: #0f2a47;
    --navy-deep: #0a1f36;
    --sky: #4aa8d8;
    --sky-light: #8fd0f0;
    --ink: #1a1a1a;
    --paper: #ffffff;
    --backdrop: #e9edf1;
    --muted: #6fa9cf;
  }
  * { box-sizing: border-box; margin: 0; padding: 0; }
  html, body { width: 1200px; height: 892px; overflow: hidden; }
  body {
    background: var(--backdrop);
    font-family: 'Play', sans-serif;
    position: relative;
  }
  .card {
    position: absolute;
    left: 280px;
    width: 640px;
    height: 366px;
    border-radius: 4px;
    overflow: hidden;
    box-shadow: 0 6px 18px rgba(10, 31, 54, 0.18);
  }
  .card--front { top: 60px; background: var(--paper); }
  .card--back { top: 466px; }

  .front-wave { position: absolute; inset: 0; }

  .brand {
    position: absolute;
    left: 40px;
    top: 52px;
    font-size: 34px;
    letter-spacing: 1px;
    color: var(--navy);
    text-transform: uppercase;
    white-space: nowrap;
  }
  .services {
    position: absolute;
    left: 42px;
    top: 96px;
    font-size: 11px;
    letter-spacing: 0.8px;
    color: var(--muted);
    white-space: nowrap;
  }
  .person { position: absolute; left: 60px; top: 140px; }
  .person__name { font-size: 25px; color: var(--sky); line-height: 1; }
  .person__role { font-size: 17px; color: var(--ink); margin-top: 4px; }

  .contacts { position: absolute; left: 40px; top: 206px; list-style: none; }
  .contacts li {
    display: flex; align-items: center; gap: 12px;
    font-size: 15px; color: var(--ink); height: 27px;
    white-space: nowrap;
  }
  .contacts svg { width: 16px; height: 16px; flex: none; }

  .abn {
    position: absolute;
    right: 16px;
    top: 40px;
    font-size: 15px;
    color: var(--paper);
    letter-spacing: 1px;
    white-space: nowrap;
  }

  .back-photo {
    position: absolute; inset: 0;
    background: linear-gradient(160deg, #1d6fb0 0%, #3c9ad6 45%, #a9d6ef 72%, #e8f4fb 100%);
  }
  .back-band {
    position: absolute; left: 0; right: 0; bottom: 0; height: 110px;
    background: rgba(10, 31, 54, 0.88);
    padding: 22px 36px;
  }
  .back-band .brand {
    position: static;
    font-size: 36px;
    color: var(--sky);
  }
  .back-band .services {
    position: static;
    margin-top: 8px;
    font-size: 13px;
  }
</style>
</head>
<body>

  <section class="card card--front" aria-label="Business card front">
    <svg class="front-wave" viewBox="0 0 640 366" preserveAspectRatio="none" aria-hidden="true">
      <path d="M446,0 C434,120 464,220 354,290 C264,345 124,355 40,366 L640,366 L640,0 Z" fill="var(--sky)"/>
      <path d="M456,0 C444,122 474,224 362,296 C274,350 144,360 76,366 L640,366 L640,0 Z" fill="var(--paper)"/>
      <path d="M462,0 C450,124 480,226 368,300 C282,352 160,362 104,366 L640,366 L640,0 Z" fill="var(--navy)"/>
    </svg>

    <div class="brand">Varnex Consulting</div>
    <div class="services">Search &amp; Select | Career | Coaching | Leadership | Outplacement</div>

    <div class="person">
      <div class="person__name">Gavin Threlkeld</div>
      <div class="person__role">Principal</div>
    </div>

    <ul class="contacts">
      <li>
        <svg viewBox="0 0 16 16" aria-hidden="true"><rect width="16" height="16" rx="2" fill="var(--sky)"/><path d="M5 4c1 0 1.5 2 1 2.6-.4.4.9 2.5 2.2 3 .5-.5 2.4 0 2.4 1 0 .8-1 1.4-1.8 1.2C6.5 11.2 4.3 8.4 4 6 3.9 5 4.2 4 5 4z" fill="#fff"/></svg>
        <span>1300 485 193</span>
      </li>
      <li>
        <svg viewBox="0 0 16 16" aria-hidden="true"><rect width="16" height="16" rx="2" fill="var(--sky)"/><rect x="3.5" y="5" width="9" height="6.5" fill="none" stroke="#fff"/><path d="M3.5 5l4.5 3.5L12.5 5" fill="none" stroke="#fff"/></svg>
        <span>career@varnexconsulting.example</span>
      </li>
      <li>
        <svg viewBox="0 0 16 16" aria-hidden="true"><rect width="16" height="16" rx="2" fill="var(--sky)"/><path d="M8 3.5a3 3 0 0 1 3 3c0 2.2-3 6-3 6s-3-3.8-3-6a3 3 0 0 1 3-3z" fill="#fff"/><circle cx="8" cy="6.5" r="1" fill="var(--sky)"/></svg>
        <span>PO Box 3172 Merrowdale NSW 2291</span>
      </li>
    </ul>

    <div class="abn">ABN: 71203948865</div>
  </section>

  <section class="card card--back" aria-label="Business card back">
    <div class="back-photo" role="img" aria-label="Photo of a snowboarder mid-jump above a snowy mountain ridge under a clear blue sky"></div>
    <div class="back-band">
      <div class="brand">Varnex Consulting</div>
      <div class="services">Search &amp; Select | Career | Coaching | Leadership | Outplacement</div>
    </div>
  </section>

</body>
</html>
```